Business Card Design for Software Development Company

I am looking for a business card design the incorporates my new logo (attached below).

Key information to include:
Name: Martin Quelbrook
Title: CEO
Email: martin@brightwellcivic.example
Phone: 555-218-9403
Website: www.brightwellcivic.example

NOTE: This design should be easy to edit so that we can order cards for different members of our team.

```html
<!DOCTYPE html>
<html lang="en">
<head>
<meta charset="utf-8">
<title>BrightwellLabs Business Card</title>
<link rel="stylesheet" href="https://fonts.googleapis.com/css2?family=Montserrat:wght@600;700&family=Poppins:wght@400;500;700&display=swap">
<style>
  :root {
    --page-bg: #7a7a7c;
    --navy: #2f4a5c;
    --navy-deep: #2b3f4f;
    --ink: #2b3f4f;
    --paper: #ffffff;
    --teal: #15a48f;
    --orange: #ef7b22;
    --red: #c0362c;
    --pattern: #3b5668;
  }
  * { box-sizing: border-box; margin: 0; padding: 0; }
  html, body { width: 900px; height: 1200px; overflow: hidden; }
  body {
    background: var(--page-bg);
    font-family: "Poppins", sans-serif;
    position: relative;
  }
  .card {
    position: absolute;
    width: 630px;
    height: 360px;
  }
  .card--front {
    left: 135px;
    top: 213px;
    background: var(--navy);
    overflow: hidden;
  }
  .front-pattern {
    position: absolute;
    inset: 0;
    background: linear-gradient(135deg, var(--navy-deep), var(--pattern));
  }
  .brand {
    position: absolute;
    display: flex;
    align-items: center;
    gap: 12px;
  }
  .brand__dot {
    width: 34px;
    height: 34px;
    border-radius: 50%;
    background: var(--orange);
    flex: none;
  }
  .brand__name {
    font-family: "Montserrat", sans-serif;
    font-weight: 600;
    letter-spacing: -0.5px;
    line-height: 1;
  }
  .brand__tagline {
    position: absolute;
    right: 0;
    font-family: "Montserrat", sans-serif;
    font-weight: 700;
    text-transform: uppercase;
    white-space: nowrap;
  }
  .card--front .brand { left: 64px; top: 148px; }
  .card--front .brand__name { font-size: 56px; color: var(--paper); }
  .card--front .brand__tagline { top: 64px; font-size: 7.5px; color: var(--paper); letter-spacing: 0.3px; }

  .card--back {
    left: 136px;
    top: 627px;
    background: var(--paper);
  }
  .card--back .brand { right: 44px; top: 44px; gap: 8px; }
  .card--back .brand__dot { width: 22px; height: 22px; }
  .card--back .brand__name { font-size: 37px; color: var(--ink); }
  .card--back .brand__tagline { top: 40px; font-size: 5px; color: var(--ink); }

  .person {
    position: absolute;
    left: 44px;
    top: 190px;
  }
  .person__name {
    font-weight: 700;
    font-size: 24px;
    color: var(--teal);
    line-height: 1.1;
  }
  .person__title {
    font-size: 14px;
    font-weight: 500;
    color: var(--ink);
    margin-top: 2px;
  }
  .person__rule {
    width: 30px;
    height: 2px;
    margin-top: 5px;
    background: linear-gradient(90deg, var(--teal), var(--orange), var(--red));
  }
  .contact-list {
    list-style: none;
    margin-top: 9px;
  }
  .contact-list li {
    display: flex;
    align-items: center;
    gap: 6px;
    font-size: 15px;
    font-weight: 500;
    color: var(--ink);
    height: 25px;
  }
  .contact-list svg { width: 15px; height: 15px; flex: none; }
  .contact--phone { letter-spacing: 2.6px; }
</style>
</head>
<body>
  <section class="card card--front">
    <div class="front-pattern" role="img" aria-label="Repeating pattern of faint brand triangles on navy"></div>
    <div class="brand">
      <span class="brand__dot"></span>
      <span class="brand__name">BrightwellLabs</span>
      <span class="brand__tagline">A division of Brightwell Civic</span>
    </div>
  </section>

  <section class="card card--back">
    <div class="brand">
      <span class="brand__dot"></span>
      <span class="brand__name">BrightwellLabs</span>
      <span class="brand__tagline">A division of Brightwell Civic</span>
    </div>

    <div class="person">
      <h1 class="person__name">Martin Quelbrook</h1>
      <p class="person__title">CEO</p>
      <div class="person__rule"></div>
      <ul class="contact-list">
        <li class="contact--phone">
          <svg viewBox="0 0 16 16" aria-hidden="true"><path d="M3 1.5l2.5-.5 1.5 3.5-1.8 1.2a9 9 0 0 0 4.6 4.6L11 8.5l3.5 1.5-.5 2.5c-.3 1.3-1.5 2-2.8 1.8C6.2 13.4 2.6 9.8 1.7 4.8 1.5 3.4 2 2 3 1.5z" fill="var(--red)"/></svg>
          555-218-9403
        </li>
        <li>
          <svg viewBox="0 0 16 16" aria-hidden="true"><rect x="1" y="3" width="14" height="10" fill="var(--orange)"/><path d="M1 3l7 5.5L15 3" fill="none" stroke="var(--teal)" stroke-width="1.6"/></svg>
          martin@brightwellcivic.example
        </li>
        <li>
          <svg viewBox="0 0 16 16" aria-hidden="true"><circle cx="8" cy="8" r="6.5" fill="none" stroke="var(--red)" stroke-width="1.4"/><ellipse cx="8" cy="8" rx="2.8" ry="6.5" fill="none" stroke="var(--orange)" stroke-width="1.2"/><path d="M1.5 8h13M2.5 5h11M2.5 11h11" stroke="var(--teal)" stroke-width="1"/></svg>
          www.brightwellcivic.example
        </li>
      </ul>
    </div>
  </section>
</body>
</html>
```